Plakat-Design Workshop gegen Prüfungsangst
Zielgruppe
Prüfungsangst überwinden mittels Workshops: 'Selbsthypnose erlernen'
Zielgruppe Studenten
Schweißausbrüche, Blackout, und Resignation.
Viele kennen diese unangenehmen Momente, wenn eine Prüfung begonnen hat und die Aufgabenstellungen scheinbar unlösbar sind.
Dann ist Entspannung nahezu unmöglich. Das Stresshormon Cortisol wurde bereits ausgeschüttet. Es beeinträchtigt die Erinnerung an das Gelernte.
Die mentale Vorbereitung sollte schon viel eher ansetzen, wenn es noch nicht zu spät ist. Wenn der Körper noch nicht verkrampft ist.
Selbsthypnose vor Prüfungen ist hier eine tolle Möglichkeit.
Mit Hilfe einer geführten Selbsthypnoseanleitung ist es Dir möglich Dein Unterbewusstsein so zu programmieren, dass diese Übererregungszustände vor Prüfungssituationen deutlich reduziert werden.
Aufgabenstellung
DINA 4 Plakat, 'Prüfungsangst?' mit einem Freifeld, wo man Ort, Datum und Zeit der Veranstaltung 'Selbsthypnose erlernen'
(Selbstsicher in die Prüfung) eindrucken kann.
darunter:
Anmeldung: Tel: 01563 8074215
Dipl. Sportl. Henrik Wolde Mentaltraining
weitere Infos auch über Einzelsitzungen: www.wolde-trancepraxis.de

```html
<!DOCTYPE html>
<html lang="de">
<head>
<meta charset="utf-8">
<title>Prüfungsangst? – Plakat</title>
<link href="https://fonts.googleapis.com/css2?family=Barlow:wght@600;700;800&family=Barlow+Condensed:wght@500;700&display=swap" rel="stylesheet">
<style>
  :root {
    --red: #e2402a;
    --red-dark: #c8321f;
    --black: #0a0a0a;
    --white: #ffffff;
    --page: #ffffff;
    --photo-top: #d9745e;
    --photo-mid: #7d8fae;
    --photo-low: #3f5a86;
  }
  * { margin: 0; padding: 0; box-sizing: border-box; }
  html, body { width: 1200px; height: 600px; overflow: hidden; background: var(--page); }
  .poster {
    position: absolute; left: 400px; top: 17px;
    width: 400px; height: 566px;
    background: var(--red);
    overflow: hidden;
    box-shadow: 4px 6px 10px rgba(0,0,0,.25);
    font-family: "Barlow", sans-serif;
    color: var(--white);
  }
  .poster__diagonal { position: absolute; inset: 0; width: 400px; height: 566px; }
  .brand {
    position: absolute; left: 117px; top: 0; width: 167px; height: 83px;
    background: var(--black);
    display: flex; flex-direction: column; align-items: center; justify-content: flex-end;
    padding-bottom: 14px;
  }
  .brand__name {
    font-family: "Barlow", sans-serif; font-weight: 800;
    font-size: 12px; letter-spacing: .5px; text-transform: uppercase; color: var(--white);
    display: flex; align-items: center; gap: 5px;
  }
  .brand__dot { width: 8px; height: 8px; border-radius: 50%; background: var(--red); }
  .brand__tagline {
    margin-top: 3px; font-family: "Barlow", sans-serif; font-weight: 600;
    font-size: 4.6px; letter-spacing: .8px; text-transform: uppercase; color: #d8d8d8;
  }
  .stage {
    position: absolute; left: 38px; top: 83px; width: 324px; height: 475px;
  }
  .stage__frame {
    position: absolute; left: 0; top: 0; width: 324px; height: 392px;
    border: 2.5px solid var(--black);
  }
  .stage__photo {
    position: absolute; left: 70px; top: 12px; width: 190px; height: 377px;
    border-radius: 60px 60px 0 0;
    background: linear-gradient(180deg, var(--photo-top) 0%, var(--photo-mid) 40%, var(--photo-low) 100%);
    opacity: .85;
  }
  .headline {
    position: absolute; left: 0; width: 324px; top: 300px; text-align: center;
    font-weight: 700; font-size: 31px; letter-spacing: 2px;
    text-shadow: 1px 2px 3px rgba(0,0,0,.45);
  }
  .subline {
    position: absolute; left: 0; width: 324px; top: 337px; text-align: center;
    font-weight: 700; font-size: 13.5px; letter-spacing: .4px;
    text-shadow: 1px 1px 2px rgba(0,0,0,.45);
  }
  .imprint { position: absolute; left: 38px; top: 484px; width: 324px; }
  .imprint__row { display: flex; align-items: center; height: 22px; }
  .imprint__label {
    width: 77px; font-weight: 800; font-size: 15px; letter-spacing: .6px;
    text-shadow: 1px 1px 2px rgba(0,0,0,.4);
  }
  .imprint__field { flex: 1; height: 16px; background: var(--white); }
  .footer {
    position: absolute; left: 0; bottom: 0; width: 400px; height: 31px;
    background: var(--black);
    display: flex; align-items: center; justify-content: center;
    font-family: "Barlow Condensed", sans-serif; font-weight: 500; font-size: 6.6px; color: var(--white);
    white-space: nowrap;
  }
  .footer strong { font-weight: 700; }
</style>
</head>
<body>
  <main class="poster">
    <svg class="poster__diagonal" viewBox="0 0 400 566" aria-hidden="true">
      <polygon points="0,395 400,247 400,566 0,566" fill="var(--red-dark)"/>
    </svg>

    <header class="brand">
      <div class="brand__name"><span class="brand__dot"></span>Wolde-Trancepraxis</div>
      <div class="brand__tagline">Kindheitsmuster auflösen - Ideen finden</div>
    </header>

    <section class="stage">
      <div class="stage__photo" role="img" aria-label="Foto: verängstigte Studentin mit Rucksack, die bunte Hefte und Ordner an sich drückt"></div>
      <div class="stage__frame"></div>
      <h1 class="headline">PRÜFUNGSANGST?</h1>
      <p class="subline">Selbstsicher in die Prüfung</p>
    </section>

    <section class="imprint">
      <div class="imprint__row"><span class="imprint__label">Datum:</span><span class="imprint__field"></span></div>
      <div class="imprint__row"><span class="imprint__label">Uhrzeit:</span><span class="imprint__field"></span></div>
    </section>

    <footer class="footer">
      <span><strong>Anmeldung:</strong> Tel.: 01563 8074215 || Dipl. Sportl. Henrik Wolde Mentaltraining || weitere Infos auch über Einzelsitzungen: <strong>www.wolde-trancepraxis.de</strong></span>
    </footer>
  </main>
</body>
</html>
```